Local fast-growing company in the service sector

We are looking for a modern business card design, which should also appear on our letterheads

Target Market(s)

Private and industrial sectors

Contact Information for Business Card

Vorname Name
Kellberger Str. 18
71409 Kellbach
Tel.: 07146-839214-0
Name@agentur-kvtl.de

Colors
9d9d9d
919191
aaaaaa

Requirements
Must have
• The logo (file) in silver

```html
<!DOCTYPE html>
<html lang="de">
<head>
<meta charset="utf-8">
<title>KVTL Visitenkarte</title>
<link rel="stylesheet" href="https://fonts.googleapis.com/css2?family=Mulish:wght@400;700;800&display=swap">
<style>
  :root {
    --page-bg: #d8d8d8;
    --card-light: #f1f1f1;
    --card-mid: #dcdcdc;
    --silver: #9d9d9d;
    --silver-mid: #919191;
    --silver-light: #aaaaaa;
    --band-dark: #3f3f40;
    --band-mid: #6a6a6b;
    --text-dark: #3a3a3a;
    --name-gold: #d8c7a4;
  }
  html, body {
    margin: 0;
    width: 1200px;
    height: 969px;
    overflow: hidden;
    background: var(--page-bg);
    font-family: "Mulish", Arial, sans-serif;
  }
  .business-card {
    position: absolute;
    left: 100px;
    top: 200px;
    width: 1000px;
    height: 570px;
    border-radius: 28px;
    overflow: hidden;
    background: linear-gradient(160deg, var(--card-light) 0%, var(--card-mid) 100%);
    box-shadow: 0 10px 30px rgba(0,0,0,0.18);
  }
  .card-band {
    position: absolute;
    inset: 0;
    width: 1000px;
    height: 570px;
  }
  .brand {
    position: absolute;
    left: 78px;
    top: 100px;
    display: flex;
    align-items: center;
    gap: 28px;
  }
  .brand-square {
    width: 110px;
    height: 110px;
    background: var(--silver);
  }
  .brand-name {
    font-weight: 800;
    font-size: 110px;
    line-height: 1;
    letter-spacing: 2px;
    color: var(--silver-mid);
  }
  .address {
    position: absolute;
    left: 78px;
    top: 326px;
    font-size: 23px;
    line-height: 32px;
    color: var(--text-dark);
  }
  .contact-list {
    position: absolute;
    left: 78px;
    top: 398px;
    margin: 0;
    padding: 0;
    list-style: none;
    font-size: 23px;
    line-height: 32px;
    color: var(--text-dark);
  }
  .contact-list li {
    display: flex;
    align-items: center;
    gap: 14px;
  }
  .contact-icon {
    width: 18px;
    height: 18px;
    flex: none;
  }
  .icon-fill { fill: var(--text-dark); }
  .icon-line { fill: none; stroke: var(--text-dark); stroke-width: 2.2; stroke-linejoin: round; }
  .person-name {
    position: absolute;
    right: 62px;
    top: 446px;
    font-weight: 700;
    font-size: 36px;
    color: var(--name-gold);
  }
</style>
</head>
<body>
  <div class="business-card">
    <svg class="card-band" viewBox="0 0 1000 570" aria-hidden="true">
      <defs>
        <linearGradient id="bandFill" x1="0" y1="0" x2="1" y2="1">
          <stop offset="0" stop-color="var(--band-mid)"/>
          <stop offset="1" stop-color="var(--band-dark)"/>
        </linearGradient>
        <linearGradient id="edgeFill" x1="0" y1="0" x2="0" y2="1">
          <stop offset="0" stop-color="#d0d0d0"/>
          <stop offset="0.5" stop-color="var(--silver-light)"/>
          <stop offset="1" stop-color="var(--silver-mid)"/>
        </linearGradient>
      </defs>
      <path d="M760 0 C850 40 880 150 800 260 L440 570 L1000 570 L1000 0 Z" fill="url(#edgeFill)"/>
      <path d="M800 0 C890 45 905 160 830 265 L490 570 L1000 570 L1000 0 Z" fill="url(#bandFill)"/>
    </svg>

    <div class="brand">
      <div class="brand-square"></div>
      <div class="brand-name">KVTL</div>
    </div>

    <div class="address">
      Kellberger Str. 18<br>
      71409 Kellbach
    </div>

    <ul class="contact-list">
      <li>
        <svg class="contact-icon" viewBox="0 0 24 24" aria-hidden="true"><path class="icon-fill" d="M6.6 10.8a15 15 0 0 0 6.6 6.6l2.2-2.2a1 1 0 0 1 1-.25 11.4 11.4 0 0 0 3.6.57 1 1 0 0 1 1 1V20a1 1 0 0 1-1 1A17 17 0 0 1 3 4a1 1 0 0 1 1-1h3.5a1 1 0 0 1 1 1c0 1.25.2 2.45.57 3.57a1 1 0 0 1-.25 1z"/></svg>
        07146-839214-0
      </li>
      <li>
        <svg class="contact-icon" viewBox="0 0 24 24" aria-hidden="true"><rect class="icon-fill" x="2" y="5" width="20" height="14" rx="1.5"/><path d="M3 6l9 7 9-7" fill="none" stroke="#dcdcdc" stroke-width="2"/></svg>
        Name@agentur-kvtl.de
      </li>
      <li>
        <svg class="contact-icon" viewBox="0 0 24 24" aria-hidden="true"><circle class="icon-line" cx="12" cy="12" r="9.5"/><ellipse class="icon-line" cx="12" cy="12" rx="4" ry="9.5"/><path class="icon-line" d="M2.5 12h19"/></svg>
        agentur-kvtl.de
      </li>
    </ul>

    <div class="person-name">Vorname Name</div>
  </div>
</body>
</html>
```